Business Card Design for Flood Rescue 360 - Property Restoration Professionals

I need a business card designed for Flood Rescue 360. We are a full-service property restoration solution. Providing water, fire, smoke & storm restoration as well as mold remediation and full remodel or reconstruction to homes and businesses across Dallas-Fort Worth, TX.
Target Market(s)
home and business owners with insurance covered property damage from water, fire or storm related damage
Industry/Entity Type
property restoration
Contact Information for Business Card
Marcus Pelley General Manager Cell: 214-555-0193 Office: 469-555-0148 email: Marcus@FloodRescue360.example services: Water, Fire, Mold, Reconstruction Tagline: Urgency for Your Water Emergency!
Look and feel
Each slider illustrates characteristics of the customer's brand and the style your logo design should communicate.

```html
<!DOCTYPE html>
<html lang="en">
<head>
<meta charset="utf-8">
<title>Flood Rescue 360 – Business Card</title>
<link rel="stylesheet" href="https://fonts.googleapis.com/css2?family=Montserrat:wght@400;500;700;800&display=swap">
<style>
  :root {
    --brand-blue: #16b4e6;
    --ink: #231f20;
    --white: #ffffff;
    --backdrop: #3b3b3d;
  }
  * { margin: 0; padding: 0; box-sizing: border-box; }
  html, body { width: 1200px; height: 1059px; overflow: hidden; }
  body {
    background: var(--backdrop);
    font-family: "Montserrat", Arial, sans-serif;
    position: relative;
  }
  .card {
    position: absolute;
    border-radius: 22px;
    box-shadow: 0 14px 24px rgba(0,0,0,0.45);
    overflow: hidden;
  }
  .card--front { left: 256px; top: 100px; width: 688px; height: 391px; background: var(--white); }
  .card--back  { left: 253px; top: 537px; width: 694px; height: 394px; background: var(--brand-blue); }

  .brand {
    position: absolute;
    display: flex;
    align-items: center;
    font-weight: 800;
    text-transform: uppercase;
    line-height: 0.95;
    letter-spacing: -0.5px;
  }
  .brand__name { display: block; }
  .brand__mark { border-radius: 50%; flex: none; }

  .card--front .brand { left: 30px; top: 162px; color: var(--brand-blue); font-size: 34px; gap: 14px; }
  .card--front .brand__mark { width: 56px; height: 56px; border: 6px solid var(--brand-blue); }

  .card--back .brand { left: 138px; top: 140px; color: var(--white); font-size: 54px; gap: 20px; }
  .card--back .brand__mark { width: 86px; height: 86px; border: 9px solid var(--white); }

  .divider { position: absolute; left: 343px; top: 106px; width: 2px; height: 184px; background: var(--brand-blue); }

  .person { position: absolute; left: 371px; top: 106px; }
  .person__name { color: var(--brand-blue); font-weight: 700; font-size: 28px; letter-spacing: 0.6px; line-height: 1; text-transform: uppercase; }
  .person__title { color: var(--ink); font-size: 16px; margin-top: 10px; letter-spacing: 0.4px; }
  .person__rule { width: 20px; height: 2px; background: var(--brand-blue); margin-top: 15px; }

  .contacts { position: absolute; left: 371px; top: 194px; width: 295px; list-style: none; }
  .contacts li { display: flex; align-items: center; height: 25px; font-size: 14.5px; color: var(--ink); letter-spacing: 0.2px; white-space: nowrap; }
  .contacts svg { width: 13px; height: 13px; margin-right: 8px; fill: var(--brand-blue); flex: none; }

  .tagline { position: absolute; left: 0; right: 0; top: 333px; text-align: center; font-size: 16px; color: var(--ink); letter-spacing: 0.5px; }

  .services { position: absolute; left: 0; right: 0; top: 333px; display: flex; justify-content: center; gap: 12px; list-style: none; color: var(--white); font-size: 18px; letter-spacing: 0.6px; }
  .services li { display: flex; align-items: center; gap: 12px; }
  .services svg { width: 12px; height: 16px; fill: var(--white); }
</style>
</head>
<body>
  <section class="card card--front" aria-label="Business card front">
    <div class="brand">
      <span class="brand__name">Flood<br>Rescue 360</span>
      <span class="brand__mark"></span>
    </div>
    <div class="divider"></div>
    <div class="person">
      <h1 class="person__name">Marcus Pelley</h1>
      <p class="person__title">General Manager</p>
      <div class="person__rule"></div>
    </div>
    <ul class="contacts">
      <li><svg viewBox="0 0 24 24"><path d="M6.6 10.8a15 15 0 0 0 6.6 6.6l2.2-2.2a1 1 0 0 1 1-.25 11.4 11.4 0 0 0 3.6.57 1 1 0 0 1 1 1V20a1 1 0 0 1-1 1A17 17 0 0 1 3 4a1 1 0 0 1 1-1h3.5a1 1 0 0 1 1 1c0 1.25.2 2.45.57 3.57a1 1 0 0 1-.25 1z"/></svg>214-555-0193</li>
      <li><svg viewBox="0 0 24 24"><path d="M7 1h10a2 2 0 0 1 2 2v18a2 2 0 0 1-2 2H7a2 2 0 0 1-2-2V3a2 2 0 0 1 2-2zm0 3v14h10V4zm5 15.5a1 1 0 1 0 0 2 1 1 0 0 0 0-2z"/></svg>469-555-0148</li>
      <li><svg viewBox="0 0 24 24"><path d="M2 5h20v14H2zm2 2v.5l8 5 8-5V7z"/></svg>Marcus@FloodRescue360.example</li>
      <li><svg viewBox="0 0 24 24"><path d="M12 2a10 10 0 1 0 0 20 10 10 0 0 0 0-20zm-1 2.1V8H7.6A8 8 0 0 1 11 4.1zm2 0A8 8 0 0 1 16.4 8H13zM4.3 10H11v4H4.3a8 8 0 0 1 0-4zM13 10h6.7a8 8 0 0 1 0 4H13zm-5.4 6H11v3.9A8 8 0 0 1 7.6 16zm5.4 0h3.4a8 8 0 0 1-3.4 3.9z"/></svg>www.FloodRescue360.example</li>
    </ul>
    <p class="tagline">Urgency for Your Water Emergency!</p>
  </section>

  <section class="card card--back" aria-label="Business card back">
    <div class="brand">
      <span class="brand__name">Flood<br>Rescue 360</span>
      <span class="brand__mark"></span>
    </div>
    <ul class="services">
      <li><svg viewBox="0 0 12 16"><path d="M6 0C6 0 0 7 0 10.5a6 6 0 0 0 12 0C12 7 6 0 6 0z"/></svg>Water</li>
      <li><svg viewBox="0 0 12 16"><path d="M6 0C6 0 0 7 0 10.5a6 6 0 0 0 12 0C12 7 6 0 6 0z"/></svg>Fire</li>
      <li><svg viewBox="0 0 12 16"><path d="M6 0C6 0 0 7 0 10.5a6 6 0 0 0 12 0C12 7 6 0 6 0z"/></svg>Mold</li>
      <li><svg viewBox="0 0 12 16"><path d="M6 0C6 0 0 7 0 10.5a6 6 0 0 0 12 0C12 7 6 0 6 0z"/></svg>Reconstruction</li>
    </ul>
  </section>
</body>
</html>
```